Application page web design and internal pages

Create a web site where home
Page looks like an application screen for a mobile phone

Use bold icons and colors with images that have round edges

PorlenPurse Apps is name of page

Search bar at the top

Use colors from Vextaro.org for background

Price of ZORBS in top right corner (https://www.quelvix.example/trade/en-US?symbol=ZORBS_USDT&layout=basic&theme=dark)

Pages within each app should be the same color as the icon

Use the following as app icons on the page:
Key
Icon name: first screen; second screen (text)

⁃ Balances: enter pin; display balances (Your account can hold multiple currency denominations. Your balances are: ZORBS 1234567890)
⁃ Transactions: enter pin; display transactions (Your last 5 payments are ZORBS 10 from Vextaro)
⁃ Send Money: enter phone number, enter amount, send button; display message
⁃ Create Account: choose country code, enter phone number, create button; enter pin; display message ( (phone number) will be notified when their account has been created)
⁃ My Wallet Address: enter pin; display public key (IMPORTANT Send only STELLAR blockchain tokens to this deposit address: GDXQ7PLM2ZNVA9TRK4WSEY8HCBUJ6FOGDLIXP3QM5RTVKNAWZEHOBCYS)
⁃ Private Message: enter phone number, enter message, choose image, send button; enter pin; display message ( (phone number) will be notified when their message has been created)
⁃ Buy Cryptocurrency: drop drown menu of cryptocurrency to purchase (Bitcoin/Ethereum/Stellar/ZORBS), Amount in USD field, amount in chosen cryptocurrency displayed, frequency drop down menu (once/daily/weekly/monthly), buy button; enter card information (name, card number, expiration date, cvv, billing address, zip code), confirm buy button, transactions will appear on your billing statement as VEXTARO; enter pin screen; display message (You will be notified when your coin is received)
⁃ NFTs: upload image, title, description, link media, create NFT button; enter pin screen; display message (You will be notified when your NFT is created)
⁃ Earn: display message (Earn cryptocurrency doing what you do everyday, coming soon)
⁃ Files/Vault: display message (Storage for your photos, documents and more, coming soon)
⁃ Wealth: display message (Build wealth by working with a financial professional to get you to the next level), check box (I would like a financial professional to contact me about building wealth), contact me button; display message (A financial professional will contact you to achieve your financial goals)
⁃ Education: display message (Learn more about everything, coming soon)
⁃ News: display message (News from around the world, coming soon)
⁃ FAQs: use FAQs from this link https://vextaro.example/faq
⁃ Contact Us: enter message, send button; display message (Thank you for reaching out. We will reply to your message in the order it was received. Your patience is appreciated. Blessings.)

Requirements
Must have
• Application home page that looks like the Home Screen of a mobile phone
Nice to have
• Colorful icons

```html
<!DOCTYPE html>
<html lang="en">
<head>
<meta charset="utf-8">
<title>PorlenPurse Apps</title>
<link href="https://fonts.googleapis.com/css2?family=Saira+Condensed:wght@400;700&family=Hind:wght@500&display=swap" rel="stylesheet">
<style>
  :root {
    --screen-bg: #1c1c46;
    --nav-bg: #212168;
    --accent: #2ad1d6;
    --label: #ffffff;
    --search-bg: #ffffff;
    --search-text: #2a2a3a;
    --price: #e82a3c;
    --tile-highlight: #262a58;
    --tile-border: #2d8fa3;
  }
  * { box-sizing: border-box; margin: 0; padding: 0; }
  html, body { width: 755px; height: 1200px; overflow: hidden; }
  body {
    background: var(--screen-bg);
    font-family: "Hind", sans-serif;
    position: relative;
  }
  .app-title {
    position: absolute; top: 58px; left: 0; width: 100%;
    text-align: center;
    font-family: "Saira Condensed", sans-serif;
    font-weight: 700; font-size: 38px; letter-spacing: 0.5px;
    color: var(--accent);
  }
  .search-bar {
    position: absolute; top: 124px; left: 0; width: 100%; height: 58px;
    background: var(--search-bg);
    display: flex; align-items: center; justify-content: space-between;
    padding: 0 40px 0 32px;
  }
  .search-bar svg { width: 30px; height: 30px; }
  .ticker {
    font-family: "Saira Condensed", sans-serif;
    font-size: 28px; color: var(--search-text);
    white-space: nowrap;
  }
  .ticker .price { color: var(--price); margin-left: 8px; }
  .app-grid {
    position: absolute; top: 244px; left: 6px;
    display: grid;
    grid-template-columns: repeat(3, 245px);
    grid-auto-rows: 158px;
  }
  .app {
    display: flex; flex-direction: column; align-items: center;
    padding-top: 16px;
  }
  .app-frame {
    display: flex; flex-direction: column; align-items: center;
    width: 200px; height: 128px; padding-top: 12px;
    border-radius: 12px;
  }
  .app.is-selected .app-frame {
    background: var(--tile-highlight);
    border: 2px solid var(--tile-border);
  }
  .app-icon {
    width: 72px; height: 70px; border-radius: 18px;
  }
  .app-label {
    margin-top: 14px;
    font-size: 18px; color: var(--label);
    letter-spacing: -0.2px; white-space: nowrap;
  }
  .icon-balances { background: linear-gradient(160deg, #3bbf9a, #ef9a5c 55%); }
  .icon-transactions { background: linear-gradient(160deg, #5fb7e6, #2f87c8); }
  .icon-send { background: linear-gradient(160deg, #ffc72c, #2aa84a 60%); }
  .icon-create { background: linear-gradient(160deg, #f2a872, #4e8fe0 60%); }
  .icon-wallet { background: linear-gradient(160deg, #f7b733, #1fb6a6 50%); }
  .icon-message { background: linear-gradient(160deg, #25b5b0, #ef4f45 45%, #f6b33a); }
  .icon-buy { background: linear-gradient(160deg, #f39a3c, #e8e8f0 60%); }
  .icon-nft { background: linear-gradient(160deg, #2fd3f0, #1b6fe0); }
  .icon-earn { background: linear-gradient(160deg, #f0c066, #5aa0e8 70%); }
  .icon-vault { background: linear-gradient(160deg, #e7484a, #2d7fc0 50%); }
  .icon-wealth { background: linear-gradient(160deg, #f5c23a, #9b6a3a 70%); }
  .icon-education { background: linear-gradient(160deg, #9aa5b5, #e84a4a 45%, #3ab86a); }
  .icon-news { background: linear-gradient(160deg, #e84a3a, #f4f0e4 40%, #f2b53a); }
  .icon-faq { background: linear-gradient(160deg, #f0457a, #4aa8e8 65%); }
  .icon-contact { background: linear-gradient(160deg, #f04e5c, #2fae5a 70%); }
  .bottom-nav {
    position: absolute; left: 0; bottom: 0; width: 100%; height: 120px;
    background: var(--nav-bg);
  }
  .nav-item {
    position: absolute; top: 32px; width: 90px; margin-left: -45px;
    display: flex; flex-direction: column; align-items: center;
    color: var(--label); font-size: 20px;
  }
  .nav-item svg { width: 46px; height: 46px; margin-bottom: 6px; }
  .nav-home { left: 292px; }
  .nav-settings { left: 440px; }
</style>
</head>
<body>
  <h1 class="app-title">PORLENPURSE APP</h1>

  <div class="search-bar">
    <svg viewBox="0 0 24 24" aria-label="Search"><circle cx="10" cy="10" r="7" fill="none" stroke="#111" stroke-width="2.6"/><line x1="15" y1="15" x2="21" y2="21" stroke="#111" stroke-width="2.8" stroke-linecap="round"/></svg>
    <div class="ticker">BTC/QVDT :<span class="price">22,546.22</span></div>
  </div>

  <main class="app-grid">
    <div class="app is-selected"><div class="app-frame"><div class="app-icon icon-balances" role="img" aria-label="Wallet with banknotes icon"></div><span class="app-label">Balances</span></div></div>
    <div class="app"><div class="app-frame"><div class="app-icon icon-transactions" role="img" aria-label="Documents with exchange arrows icon"></div><span class="app-label">Transactions</span></div></div>
    <div class="app"><div class="app-frame"><div class="app-icon icon-send" role="img" aria-label="Paper plane with coin icon"></div><span class="app-label">Send Money</span></div></div>

    <div class="app"><div class="app-frame"><div class="app-icon icon-create" role="img" aria-label="Add user icon"></div><span class="app-label">Create Account</span></div></div>
    <div class="app"><div class="app-frame"><div class="app-icon icon-wallet" role="img" aria-label="Crypto wallet icon"></div><span class="app-label">My Wallet Address</span></div></div>
    <div class="app"><div class="app-frame"><div class="app-icon icon-message" role="img" aria-label="Locked chat bubbles icon"></div><span class="app-label">Private Message</span></div></div>

    <div class="app"><div class="app-frame"><div class="app-icon icon-buy" role="img" aria-label="Shopping cart with crypto box icon"></div><span class="app-label">Buy Cryptocurrency</span></div></div>
    <div class="app"><div class="app-frame"><div class="app-icon icon-nft" role="img" aria-label="NFT hexagon badge icon"></div><span class="app-label">NFTs</span></div></div>
    <div class="app"><div class="app-frame"><div class="app-icon icon-earn" role="img" aria-label="Hand holding money bag icon"></div><span class="app-label">Earn</span></div></div>

    <div class="app"><div class="app-frame"><div class="app-icon icon-vault" role="img" aria-label="Open safe vault icon"></div><span class="app-label">Files/Vault</span></div></div>
    <div class="app"><div class="app-frame"><div class="app-icon icon-wealth" role="img" aria-label="Money bag with gold coins icon"></div><span class="app-label">Wealth</span></div></div>
    <div class="app"><div class="app-frame"><div class="app-icon icon-education" role="img" aria-label="Graduation cap on books icon"></div><span class="app-label">Education</span></div></div>

    <div class="app"><div class="app-frame"><div class="app-icon icon-news" role="img" aria-label="Newspaper icon"></div><span class="app-label">News</span></div></div>
    <div class="app"><div class="app-frame"><div class="app-icon icon-faq" role="img" aria-label="Question chat bubbles icon"></div><span class="app-label">FAQs</span></div></div>
    <div class="app"><div class="app-frame"><div class="app-icon icon-contact" role="img" aria-label="Phone and envelope icon"></div><span class="app-label">Contact Us</span></div></div>
  </main>

  <nav class="bottom-nav">
    <div class="nav-item nav-home">
      <svg viewBox="0 0 48 48" aria-hidden="true"><path d="M4 24 L24 6 L44 24" fill="none" stroke="#2ad1d6" stroke-width="5" stroke-linecap="round" stroke-linejoin="round"/><rect x="32" y="8" width="6" height="10" fill="#2ad1d6"/><path d="M10 24 V42 H20 V31 H28 V42 H38 V24 L24 12 Z" fill="#2ad1d6"/></svg>
      <span>Home</span>
    </div>
    <div class="nav-item nav-settings">
      <svg viewBox="0 0 48 48" aria-hidden="true"><g fill="#2ad1d6"><circle cx="24" cy="24" r="15"/><rect x="20" y="2" width="8" height="10" rx="2"/><rect x="20" y="36" width="8" height="10" rx="2"/><rect x="2" y="20" width="10" height="8" rx="2"/><rect x="36" y="20" width="10" height="8" rx="2"/><rect x="20" y="2" width="8" height="10" rx="2" transform="rotate(45 24 24)"/><rect x="20" y="2" width="8" height="10" rx="2" transform="rotate(135 24 24)"/><rect x="20" y="2" width="8" height="10" rx="2" transform="rotate(225 24 24)"/><rect x="20" y="2" width="8" height="10" rx="2" transform="rotate(315 24 24)"/></g><circle cx="24" cy="24" r="7" fill="#212168"/></svg>
      <span>Settings</span>
    </div>
  </nav>
</body>
</html>
```